New Year's card HTML

can you produce a best new years wishes 2018 design in HTML for our website as what I would like to send by email towards my network of candidates / customers ...

It must be wow, inspiring , design, meaningfull... MMM those people care about me, or those people will help me to go the extra mile, to help me to achieve my career goals, Your best move, enhance my possibilities, bring the love back

Target Market(s)

CEo's / CMO's/ HRDirectors network of 450k

Coding

Coded - Design and coding required

Number of Pages Required

1 page

Colors

Designer to choose colors to be used in the design.

Requirements
Must have
• Logo / visual / website adress www.moravintel.com and a call to action
Should not have
• no sound as our business is confidential

```html
<!DOCTYPE html>
<html lang="en">
<head>
<meta charset="utf-8">
<title>Happy New Year 2018 – Moravintel</title>
<link rel="stylesheet" href="https://fonts.googleapis.com/css2?family=Anton&family=Roboto:wght@500;700;900&display=swap">
<style>
  :root {
    --glow-yellow: #ffd84a;
    --warm-orange: #ff8a1c;
    --deep-orange: #e2550e;
    --ember: #b8360a;
    --long-shadow: rgba(140, 35, 0, 0.32);
    --silver-light: #ffffff;
    --silver-dark: #d2d2d2;
    --white: #ffffff;
  }
  html, body {
    margin: 0;
    padding: 0;
    overflow: hidden;
    background: var(--deep-orange);
  }
  .card {
    position: relative;
    width: 1200px;
    height: 933px;
    overflow: hidden;
    font-family: "Roboto", Arial, sans-serif;
    color: var(--white);
  }
  .card__backdrop {
    position: absolute;
    inset: 0;
    background:
      radial-gradient(circle at 95% 8%, rgba(255, 226, 120, 0.95) 0%, rgba(255, 200, 80, 0.5) 22%, transparent 45%),
      radial-gradient(circle at 100% 70%, rgba(255, 215, 90, 0.75) 0%, transparent 35%),
      radial-gradient(circle at 5% 15%, rgba(255, 190, 40, 0.6) 0%, transparent 30%),
      radial-gradient(circle at 15% 90%, rgba(170, 40, 5, 0.55) 0%, transparent 45%),
      linear-gradient(135deg, var(--warm-orange) 0%, var(--deep-orange) 55%, var(--warm-orange) 100%);
  }
  .card__shadow {
    position: absolute;
    inset: 0;
  }
  .brand {
    position: absolute;
    left: 82px;
    top: 40px;
    font-family: "Roboto", Arial, sans-serif;
    font-weight: 500;
    font-size: 30px;
    letter-spacing: 2px;
    line-height: 36px;
  }
  .year-tag {
    position: absolute;
    left: 526px;
    top: 104px;
    font-family: "Roboto", Arial, sans-serif;
  }
  .year-tag__label {
    display: block;
    font-weight: 700;
    font-size: 16px;
    line-height: 18px;
  }
  .year-tag__number {
    display: block;
    font-weight: 900;
    font-size: 60px;
    line-height: 56px;
    letter-spacing: -1px;
    color: #f6a35a;
    text-shadow: 0 -2px 0 #fff3e0, 2px 4px 4px rgba(120, 40, 0, 0.55);
  }
  .greeting {
    position: absolute;
    left: 0;
    width: 1224px;
    margin: 0;
    text-align: center;
    font-family: "Anton", "Impact", sans-serif;
    font-weight: 400;
    font-size: 226px;
    line-height: 164px;
    letter-spacing: 14px;
    background: linear-gradient(180deg, var(--silver-light) 0%, var(--silver-dark) 55%, #f4f4f4 100%);
    -webkit-background-clip: text;
    background-clip: text;
    color: transparent;
    transform: scaleX(1.08);
    transform-origin: 612px 0;
  }
  .greeting--happy { top: 188px; }
  .greeting--new   { top: 372px; }
  .greeting--year  { top: 557px; }
  .cta {
    position: absolute;
    left: 499px;
    top: 825px;
    width: 203px;
    height: 54px;
    box-sizing: border-box;
    border: 1px solid var(--white);
    display: flex;
    align-items: center;
    justify-content: center;
    color: var(--white);
    text-decoration: none;
    font-weight: 500;
    font-size: 23px;
  }
</style>
</head>
<body>
  <main class="card">
    <div class="card__backdrop" role="img" aria-label="Warm orange and golden background with soft glowing bokeh lights"></div>

    <svg class="card__shadow" width="1200" height="933" viewBox="0 0 1200 933" aria-hidden="true">
      <polygon points="299,190 927,190 927,352 845,560 845,721 520,933 0,933 0,640" fill="var(--long-shadow)"/>
    </svg>

    <div class="brand">MORAVINTEL</div>

    <div class="year-tag">
      <span class="year-tag__label">Loading</span>
      <span class="year-tag__number">2018</span>
    </div>

    <h1 class="greeting greeting--happy">HAPPY</h1>
    <p class="greeting greeting--new">NEW</p>
    <p class="greeting greeting--year">YEAR</p>

    <a class="cta" href="https://www.moravintel.com">Visit Our Site</a>
  </main>
</body>
</html>
```